Business Card Design Project

We are a construction company in Orange County, CA. We need a two sided business card. We would like the back to be our logo with web URL. Front should included Name, title, address, phone, fax and email address.

our address is
627 West Dorrance Blvd, Suite 308
Anaheim, CA 92718

Our logo files are attached.

Construction

```html
<!DOCTYPE html>
<html lang="en">
<head>
<meta charset="utf-8">
<title>Keldan Business Card</title>
<link rel="stylesheet" href="https://fonts.googleapis.com/css2?family=Archivo+Black&family=Arimo:wght@400&family=Lato:wght@400;700&family=Lora:wght@400&display=swap">
<style>
  :root {
    --brand-blue: #1d4f8c;
    --brand-blue-deep: #12386a;
    --brand-blue-light: #2f6fb8;
    --paper: #ffffff;
    --paper-shade: #eceef1;
    --ink: #222222;
    --backdrop: #e4e2de;
  }
  * { margin: 0; padding: 0; box-sizing: border-box; }
  html, body { width: 1200px; height: 900px; overflow: hidden; }
  body {
    background: var(--backdrop);
    font-family: "Lato", sans-serif;
    display: flex;
    flex-direction: column;
    align-items: center;
    justify-content: center;
    gap: 50px;
  }
  .card {
    position: relative;
    width: 630px;
    height: 360px;
    border-radius: 26px;
    overflow: hidden;
    box-shadow: 0 6px 18px rgba(0,0,0,0.18);
  }

  /* Back side */
  .card-back { background: var(--paper); }
  .card-back .logo-block {
    position: absolute;
    top: 96px; left: 0; right: 0;
    text-align: center;
  }
  .wordmark {
    font-family: "Archivo Black", sans-serif;
    font-size: 96px;
    line-height: 1;
    letter-spacing: -2px;
  }
  .card-back .wordmark { color: var(--brand-blue); }
  .card-back .web {
    margin-top: 6px;
    font-family: "Arimo", sans-serif;
    font-size: 17px;
    color: var(--brand-blue);
  }
  .card-back .tagline-band {
    position: absolute;
    left: 0; right: 0; bottom: 0;
    height: 78px;
    background: var(--brand-blue);
    color: var(--paper);
    display: flex;
    align-items: center;
    justify-content: center;
    font-size: 24px;
    letter-spacing: 8px;
  }

  /* Front side */
  .card-front {
    background: radial-gradient(ellipse at 50% 40%, var(--brand-blue-light) 0%, var(--brand-blue) 55%, var(--brand-blue-deep) 100%);
  }
  .name-tag {
    position: absolute;
    top: 26px; right: 0;
    height: 52px;
    padding: 0 20px 0 18px;
    background: linear-gradient(180deg, #eef1f5 0%, #c9d1dc 100%);
    display: flex;
    align-items: center;
    gap: 12px;
  }
  .name-tag .person {
    font-family: "Lora", serif;
    font-size: 23px;
    color: var(--brand-blue-deep);
  }
  .name-tag .title {
    border-left: 1px solid var(--brand-blue-deep);
    padding-left: 10px;
    font-family: "Lora", serif;
    font-size: 11px;
    line-height: 1.25;
    color: var(--brand-blue-deep);
    text-transform: uppercase;
  }
  .card-front .logo-block {
    position: absolute;
    top: 112px; left: 0; right: 0;
    text-align: center;
  }
  .card-front .wordmark { color: var(--paper); font-size: 86px; }
  .card-front .tagline {
    margin-top: 2px;
    font-size: 14px;
    letter-spacing: 5px;
    color: #cfdcee;
  }
  .contact-strip {
    position: absolute;
    left: 0; right: 0; bottom: 0;
    height: 100px;
    background: linear-gradient(180deg, var(--paper) 0%, var(--paper-shade) 100%);
    text-align: center;
    font-family: "Arimo", sans-serif;
    padding-top: 18px;
  }
  .contact-strip .address { font-size: 17px; color: var(--brand-blue); }
  .contact-strip .lines {
    margin-top: 8px;
    font-size: 15px;
    color: var(--ink);
  }
</style>
</head>
<body>
  <section class="card card-back" aria-label="Card back">
    <div class="logo-block">
      <div class="wordmark">KELDAN</div>
      <div class="web">www.keldanbuild.com</div>
    </div>
    <div class="tagline-band">PLAN • DEVELOP • CONSTRUCT</div>
  </section>

  <section class="card card-front" aria-label="Card front">
    <div class="name-tag">
      <span class="person">Marcus Hadley</span>
      <span class="title">General<br>Manager</span>
    </div>
    <div class="logo-block">
      <div class="wordmark">KELDAN</div>
      <div class="tagline">PLAN • DEVELOP • CONSTRUCT</div>
    </div>
    <div class="contact-strip">
      <div class="address">627 West Dorrance Blvd, Suite 308 Anaheim, CA 92718</div>
      <div class="lines">Phone: +1.714.555.0142 | Mobile: +1.714.555.0187 &nbsp;Mail: info@keldanbuild.com</div>
    </div>
  </section>
</body>
</html>
```